Luxury modern loose tea company web design

I am a high-end modern luxury loose leaf tea business. I have a website domain that is hosted on Shopify. I’m looking for designers that have a modern flair and are able to create websites that would easily attract major YouTube and Instagram influencers as well as a modern millennial.

Luxury is at the fore front of the design scheme and branding and should be incorporated in ALL aspects of the website. As well if designers are able to implement any unique features to make the shopping experience more fun and memorable that is a major bonus. The main colors I work with are black, silver and gold, once again reinforcing the luxury feel.

My brand is called Sip of Lume

Target Market(s)

The Modern Millenial, 21-40 (bullseye 28). He or she is a young professional that has a disposable income in which they do like to indulge with. They balance their demanding work schedules well and they have a work hard/play hard mindset. This professional is more likely to order their daily coffee from Brewvant as opposed to Ned Kallory and their social media profiles are a big indicator as to their hobbies and lifestyles outside of their work environment. They enjoy shopping at stores like Vexa, Halcyne, UrbanLoom/UrbanGent and for special occasions are willing to splurge at stores like Marlowe's, Hall Verdine and… They live a pretty active lifestyle and are highly influenced by social media trending products

Colors

Designer to choose colors to be used in the design.

Requirements
Must have
• luxury feel
• unique customer experience

```html
<!DOCTYPE html>
<html lang="en">
<head>
<meta charset="utf-8">
<title>Sip of Lume — Luxury Loose Leaf Tea</title>
<link rel="stylesheet" href="https://fonts.googleapis.com/css2?family=Roboto:wght@300;400;500;700;900&family=Poppins:wght@300;400;500;600&display=swap">
<style>
:root{
  --gold:#d6a23c;
  --gold-dark:#b88a2e;
  --ink:#222222;
  --text:#4a4a4a;
  --muted:#8a8a8a;
  --rule:#d9d9d9;
  --band:#efefef;
  --card:#ffffff;
  --footer:#121212;
  --footer-text:#e6e6e6;
  --white:#ffffff;
}
*{margin:0;padding:0;box-sizing:border-box}
html,body{width:1200px;height:3651px;overflow:hidden;background:var(--white)}
body{position:relative;font-family:"Poppins",sans-serif;color:var(--text)}
.abs{position:absolute}

/* header */
.site-header{position:absolute;left:0;top:0;width:1200px;height:85px;background:var(--white)}
.brand{position:absolute;left:132px;top:22px;font-family:"Roboto",sans-serif;font-weight:400;font-size:34px;color:var(--ink);letter-spacing:1px}
.nav{position:absolute;left:376px;top:32px;display:flex;gap:0;font-family:"Roboto",sans-serif;font-weight:500;font-size:15px;color:var(--ink);letter-spacing:.3px}
.nav span{margin-right:42px}
.nav-icons{position:absolute;left:992px;top:28px;display:flex;gap:24px}
.cart-badge{position:absolute;left:1052px;top:28px;width:13px;height:13px;border-radius:50%;background:var(--gold)}

/* hero */
.hero{position:absolute;left:0;top:85px;width:1200px;height:572px;background:linear-gradient(160deg,#8a7a52 0%,#6e6a3a 35%,#4a3a22 70%,#2e2418 100%)}
.hero-title{position:absolute;left:0;top:232px;width:1200px;text-align:center;font-family:"Roboto",sans-serif;font-weight:900;font-size:56px;line-height:60px;color:var(--white);text-shadow:0 2px 6px rgba(0,0,0,.35)}
.hero-arrow{position:absolute;top:290px;width:30px;height:30px;border-radius:50%;background:rgba(0,0,0,.75)}
.hero-edge{position:absolute;left:0;top:635px;width:1200px;height:22px;background:var(--white)}

/* intro */
.section-title{font-family:"Roboto",sans-serif;font-weight:400;font-size:38px;color:var(--ink)}
.section-title em{font-style:normal;font-weight:500;color:var(--gold)}
.copy{font-size:12.5px;line-height:24px;color:var(--text)}
.btn-outline{position:absolute;border:2px solid #666;font-family:"Roboto",sans-serif;font-size:13px;letter-spacing:1px;color:#444;text-align:center;line-height:27px}
.frame{position:absolute;background:var(--gold)}
.photo{position:absolute}

/* product */
.price{font-family:"Roboto",sans-serif;font-size:19px;font-weight:500}
.price s{color:#777;font-weight:400;margin-right:6px}
.price b{color:var(--gold);font-weight:500}
.qty{position:absolute;border:1.5px solid #777;text-align:center;font-size:14px;line-height:31px;color:#333}
.btn-gold{position:absolute;background:var(--gold-dark);color:var(--white);font-family:"Roboto",sans-serif;font-weight:500;font-size:13px;letter-spacing:.6px;text-align:center;line-height:34px}
.share{position:absolute;display:flex;gap:10px;font-size:9px;color:#555;letter-spacing:.4px}
.share span{border:1px solid var(--rule);padding:3px 8px;display:flex;align-items:center;gap:5px}
.share i{display:inline-block;width:9px;height:9px;border-radius:2px}

/* testimonials */
.testimonials{position:absolute;left:0;top:1740px;width:1200px;height:514px;background:var(--band)}
.testimonials h2{position:absolute;left:0;top:68px;width:1200px;text-align:center;font-family:"Roboto",sans-serif;font-weight:700;font-size:38px;color:var(--ink)}
.quote-card{position:absolute;top:183px;width:289px;height:229px;background:var(--card);box-shadow:0 1px 4px rgba(0,0,0,.1);text-align:center}
.quote-mark{font-family:"Roboto",sans-serif;font-size:68px;color:#9a9a9a;line-height:60px;margin-top:22px;font-weight:700}
.quote-text{font-size:12.5px;line-height:24px;color:var(--text);padding:0 20px;margin-top:6px}
.quote-name{font-size:13px;color:var(--gold);margin-top:16px}

/* gallery */
.gallery{position:absolute;left:0;top:2254px;width:1200px;height:448px;display:flex}

/* featured */
.featured-title{position:absolute;left:0;top:2780px;width:1200px;text-align:center;font-family:"Roboto",sans-serif;font-size:32px;font-weight:400;color:var(--ink);letter-spacing:.5px}
.featured-title em{font-style:normal;font-weight:700;color:var(--gold)}
.product{position:absolute;top:2889px;width:218px}
.product .thumb{width:218px;height:208px;border:1px solid var(--rule);padding:5px;background:var(--white)}
.product .thumb div{width:100%;height:100%}
.product .name{margin-top:30px;font-size:14px;line-height:22px;color:var(--ink)}
.product .cost{margin-top:10px;font-size:16px;font-style:italic;color:var(--gold)}

/* footer */
.site-footer{position:absolute;left:0;top:3298px;width:1200px;height:353px;background:var(--footer);color:var(--footer-text)}
.footer-links{position:absolute;left:132px;top:42px;font-size:12px;line-height:24px}
.news-title{position:absolute;left:640px;top:50px;font-family:"Roboto",sans-serif;font-weight:700;font-size:17px;letter-spacing:.5px}
.news-input{position:absolute;left:640px;top:82px;width:313px;height:38px;background:var(--white);color:#555;font-size:12px;line-height:38px;padding-left:14px}
.news-btn{position:absolute;left:953px;top:82px;width:114px;height:38px;background:#a37b35;color:var(--white);font-family:"Roboto",sans-serif;font-weight:700;font-size:16px;text-align:center;line-height:38px}
.footer-rule{position:absolute;left:132px;top:166px;width:936px;height:1px;background:#333}
.follow{position:absolute;left:132px;top:222px;font-family:"Roboto",sans-serif;font-size:17px}
.social{position:absolute;left:238px;top:222px;display:flex;gap:6px}
.social span{width:24px;height:24px;border:1.5px solid var(--footer-text);border-radius:50%}
.footer-brand{position:absolute;left:0;top:208px;width:1200px;text-align:center;font-family:"Roboto",sans-serif;font-size:34px;color:var(--footer-text)}
.cards{position:absolute;left:892px;top:214px;display:flex;gap:8px}
.cards span{width:38px;height:25px;border-radius:3px;background:#d7d7d7}
.copyright{position:absolute;left:0;top:308px;width:1200px;text-align:center;font-size:11px;color:var(--footer-text)}
</style>
</head>
<body>

<header class="site-header">
  <div class="brand">Sip of Lume</div>
  <nav class="nav">
    <span>HOME</span><span>PRODUCTS</span><span>ABOUT US</span><span>LEAF TEA</span><span>BLOG</span><span>CONTACT</span>
  </nav>
  <div class="nav-icons">
    <svg width="22" height="22" viewBox="0 0 22 22"><circle cx="9" cy="9" r="6.5" fill="none" stroke="#222" stroke-width="2.6"/><line x1="14" y1="14" x2="20" y2="20" stroke="#222" stroke-width="3" stroke-linecap="round"/></svg>
    <svg width="24" height="22" viewBox="0 0 24 22"><path d="M2 8h20l-3 12H5z" fill="#222"/><path d="M7 8l5-6 5 6" fill="none" stroke="#222" stroke-width="2"/></svg>
  </div>
  <div class="cart-badge"></div>
</header>

<section class="hero" role="img" aria-label="Glass cup of green tea on a saucer beside a heap of dried loose tea leaves">
  <div class="hero-title">SIP OF LUME<br>LOOSE LEAF TEA</div>
  <div class="hero-arrow" style="left:82px"><svg width="30" height="30" viewBox="0 0 30 30"><path d="M17 10l-5 5 5 5" fill="none" stroke="#fff" stroke-width="2.4"/></svg></div>
  <div class="hero-arrow" style="left:1102px"><svg width="30" height="30" viewBox="0 0 30 30"><path d="M13 10l5 5-5 5" fill="none" stroke="#fff" stroke-width="2.4"/></svg></div>
</section>
<svg class="abs" style="left:0;top:628px" width="1200" height="30" viewBox="0 0 1200 30" preserveAspectRatio="none"><path d="M0 12 L60 8 L140 14 L220 6 L300 13 L400 7 L480 12 L560 5 L650 13 L740 8 L820 14 L900 6 L980 12 L1060 7 L1140 13 L1200 9 V30 H0Z" fill="#fff"/></svg>

<section class="intro">
  <h2 class="section-title abs" style="left:132px;top:772px">Luxury Loose <em>Leaf Tea</em></h2>
  <p class="copy abs" style="left:132px;top:842px;width:490px">Sed ut perspiciatis unde omnis iste natus error sit voluptatem accusantium doloreue laudantium, totam rem aperiam, eaque ipsa quae ab illo inventore veritatis et quasi architecto beatae vitae dicta sunt explicabo. Nemo enim ipsam voluptatem quia voluptas sit aspernatur aut odit aut fugit, sed quia cnitur magni dolores eos qui ratione voluptatem sequi nesciunt. Neque porro quisquam est, qui dolorem ipsum quia dolor sit amet, consectetur</p>
  <div class="btn-outline" style="left:132px;top:1036px;width:118px;height:31px">READ MORE</div>
  <div class="frame" style="left:693px;top:750px;width:376px;height:345px"></div>
  <div class="photo" style="left:677px;top:766px;width:376px;height:329px;background:linear-gradient(135deg,#efe4d6 0%,#c98f5e 45%,#7a4a2a 80%,#3e2a1c 100%)" role="img" aria-label="Clay teapot and glass cups of amber tea with a pile of loose tea leaves"></div>
</section>

<section class="product-feature">
  <div class="frame" style="left:148px;top:1188px;width:375px;height:424px"></div>
  <div class="photo" style="left:134px;top:1204px;width:376px;height:402px;background:linear-gradient(135deg,#6f6f6f 0%,#2a2a2a 40%,#151515 70%,#5a5a5a 100%)" role="img" aria-label="Black gift box of loose leaf tea on a grey wooden table"></div>
  <h2 class="section-title abs" style="left:560px;top:1196px">About <em>Our Product</em></h2>
  <div class="price abs" style="left:560px;top:1256px"><s>$40.00</s><b>$35.00 Sale</b></div>
  <div class="qty" style="left:562px;top:1305px;width:117px;height:34px">1</div>
  <div class="btn-gold" style="left:690px;top:1305px;width:220px;height:34px">ADD TO CART</div>
  <p class="copy abs" style="left:560px;top:1362px;width:510px;line-height:24px">Sed ut perspiciatis unde omnis iste natus error sit voluptatem accusantium doloreue laudantium, totam rem aperiam, eaque ipsa quae ab illo inventore veritatis et quasi architecto beatae vitae dicta sunt explicabo. Nemo enim ipsam voluptatem quia voluptas sit aspernatur aut odit aut fugit, sed quia consequuntur magni dolores eos qui ratione voluptatem sequi nesciunt. Neque porro quisquam est, qui dolorem ipsum quia dolor sit amet, consectetur</p>
  <div class="share" style="left:562px;top:1553px">
    <span><i style="background:#3b5998"></i>SHARE</span>
    <span><i style="background:#55acee"></i>TWEET</span>
    <span><i style="background:#cb2027;border-radius:50%"></i>PIN IT</span>
  </div>
</section>

<section class="testimonials">
  <h2>Testimonials</h2>
  <div class="quote-card" style="left:133px">
    <div class="quote-mark">“</div>
    <p class="quote-text">Nemo enim ipsam vptatem quia vtas sit aspernatur aut odit aut fugit, sed quia consequuntur magni dolores eos qui ratione voluptatem sequi</p>
    <div class="quote-name">-Ashby R.</div>
  </div>
  <div class="quote-card" style="left:455px">
    <div class="quote-mark">“</div>
    <p class="quote-text">Nemo enim ipsam vptatem quia vtas sit aspernatur aut odit aut fugit, sed quia consequuntur magni dolores eos qui ratione voluptatem sequi</p>
    <div class="quote-name">-Ashby R.</div>
  </div>
  <div class="quote-card" style="left:774px">
    <div class="quote-mark">“</div>
    <p class="quote-text">Nemo enim ipsam vptatem quia vtas sit aspernatur aut odit aut fugit, sed quia consequuntur magni dolores eos qui ratione voluptatem sequi</p>
    <div class="quote-name">-Ashby R.</div>
  </div>
</section>

<section class="gallery">
  <div style="width:600px;height:448px;background:linear-gradient(150deg,#3a2a20 0%,#5b3a22 45%,#a0602e 60%,#2c2019 100%)" role="img" aria-label="Wooden spoon resting on a bed of dark loose tea leaves"></div>
  <div style="width:600px;height:448px;background:linear-gradient(150deg,#4a4a4a 0%,#1c1c1c 45%,#0f0f0f 65%,#6a6a66 100%)" role="img" aria-label="Black tea gift box on a wooden surface"></div>
</section>

<section class="featured">
  <h2 class="featured-title"><em>FEATURED</em> COLLECTION</h2>
  <div class="product" style="left:132px">
    <div class="thumb"><div style="background:linear-gradient(135deg,#5a5a5a,#1e1e1e 60%,#3a3a3a)" role="img" aria-label="Dark black loose leaf tea"></div></div>
    <p class="name">Nemo enim ipsam voluptatem quia voluptas sit</p>
    <p class="cost">$89.95</p>
  </div>
  <div class="product" style="left:372px">
    <div class="thumb"><div style="background:linear-gradient(135deg,#f2efe8,#b89060 55%,#5c4226)" role="img" aria-label="Golden twisted loose leaf tea"></div></div>
    <p class="name">Nemo enim ipsam voluptatem quia voluptas sit</p>
    <p class="cost">$89.95</p>
  </div>
  <div class="product" style="left:612px">
    <div class="thumb"><div style="background:linear-gradient(135deg,#e8e2d0,#c98a2a 50%,#4a3a20)" role="img" aria-label="Loose leaf tea blended with orange flower petals"></div></div>
    <p class="name">Nemo enim ipsam voluptatem quia voluptas sit</p>
    <p class="cost">$89.95</p>
  </div>
  <div class="product" style="left:852px">
    <div class="thumb"><div style="background:linear-gradient(135deg,#f4f2ee,#b07a4a 50%,#3a2a20)" role="img" aria-label="Wooden bowl and scoop of rolled loose tea"></div></div>
    <p class="name">Nemo enim ipsam voluptatem quia voluptas sit</p>
    <p class="cost">$89.95</p>
  </div>
</section>

<footer class="site-footer">
  <div class="footer-links">Products<br>About Us<br>Blog<br>Contact</div>
  <div class="news-title">SIGN UP FOR NEWSLETTER</div>
  <div class="news-input">Enter email</div>
  <div class="news-btn">SIGN UP</div>
  <div class="footer-rule"></div>
  <div class="follow">Follow us</div>
  <div class="social"><span></span><span></span><span></span><span></span></div>
  <div class="footer-brand">Sip of Lume</div>
  <div class="cards"><span></span><span></span><span></span><span></span></div>
  <div class="copyright">© Copyright 2018 sipoflume. All Rights Reserved. &nbsp;Privacy Policy &nbsp;| &nbsp;Disclaimer &nbsp;| &nbsp;Terms &amp; Conditions</div>
</footer>

</body>
</html>
```